Exciting & Elegant Stationary Pack

Stationary consists of
1. Letter head / Envelope
2. Business Card
3. Invoice
4. 40x40mm sticker

Attached files;

1. Logo (Other formats available on request)
2. MS word Doc - For information and description of design
3. Website image (This will be our new website so use the colours so everything ties together)
4. Sample of stationary pack we like, but feel free to be creative

Target Market(s)

Home improvement

Industry/Entity Type

Construction

Font styles to use
Other font styles liked:
• Leave up to designer - We like font used on (website attached image)

Requirements
Must have
• Please look at uploaded file of sample website and use colours
Nice to have
• Any type of business card design - eg. metal, die cut, embossed, etc...

```html
<!DOCTYPE html>
<html lang="en">
<head>
<meta charset="utf-8">
<title>Grout &amp; Grade Letterhead</title>
<link href="https://fonts.googleapis.com/css2?family=Open+Sans:wght@400;600;800&display=swap" rel="stylesheet">
<style>
  :root {
    --navy: #1d2a4d;
    --red: #d1252e;
    --sky: #9fc8ea;
    --ink: #2b2b2b;
    --muted: #555555;
    --paper: #ffffff;
    --header-tint: #eef0f2;
  }
  * { box-sizing: border-box; margin: 0; padding: 0; }
  html, body { width: 828px; height: 1200px; overflow: hidden; background: var(--paper); }
  body { font-family: "Open Sans", Arial, sans-serif; color: var(--ink); position: relative; }

  .letterhead-top {
    position: absolute; left: 0; top: 0; width: 828px; height: 250px;
    background: linear-gradient(180deg, var(--paper) 0%, var(--header-tint) 100%);
  }
  .brand {
    position: absolute; left: 56px; top: 120px;
    display: flex; align-items: center; gap: 14px;
  }
  .brand-square { width: 34px; height: 34px; background: var(--red); }
  .brand-name {
    font-weight: 800; font-size: 44px; color: var(--navy);
    letter-spacing: 1px; text-transform: uppercase; line-height: 1;
  }

  .abn-band {
    position: absolute; left: 330px; right: 0; top: 214px; height: 36px;
    background: var(--red); color: #fff;
    font-weight: 600; font-size: 15px; letter-spacing: 0.5px;
    display: flex; align-items: center; justify-content: flex-end; padding-right: 40px;
  }
  .contact-band {
    position: absolute; left: 0; right: 0; top: 250px; height: 36px;
    background: var(--sky); color: var(--navy);
    display: flex; align-items: center; gap: 22px; padding-left: 56px;
    font-size: 14px; font-weight: 600;
  }
  .contact-item { display: flex; align-items: center; gap: 6px; }
  .contact-item svg { width: 15px; height: 15px; fill: var(--navy); }

  .letter-body {
    position: absolute; left: 56px; right: 56px; top: 380px;
    font-size: 12.5px; line-height: 1.65; color: var(--muted);
  }
  .salutation { font-size: 24px; color: var(--ink); margin-bottom: 34px; }
  .letter-body p.para { margin-bottom: 22px; }
  .sign-off { margin-top: 28px; }
  .signature-mark { width: 130px; height: 40px; margin: 14px 0 6px; background: linear-gradient(90deg, #e4e4e4, #f4f4f4); }
  .signer { line-height: 1.5; }
</style>
</head>
<body>
  <header class="letterhead-top">
    <div class="brand">
      <span class="brand-name">Grout &amp; Grade</span>
      <span class="brand-square"></span>
    </div>
  </header>

  <div class="abn-band">ABN: 12 345 678 901</div>

  <div class="contact-band">
    <span class="contact-item">
      <svg viewBox="0 0 24 24"><path d="M12 2a7 7 0 0 0-7 7c0 5 7 13 7 13s7-8 7-13a7 7 0 0 0-7-7zm0 9.5a2.5 2.5 0 1 1 0-5 2.5 2.5 0 0 1 0 5z"/></svg>
      PO Box 482 Marlow Heights NSW 2199
    </span>
    <span class="contact-item">
      <svg viewBox="0 0 24 24"><path d="M2 5h20v14H2z M3 6l9 7 9-7" fill="none" stroke="#1d2a4d" stroke-width="2"/></svg>
      hello@groutandgrade.com.au
    </span>
    <span class="contact-item">
      <svg viewBox="0 0 24 24"><circle cx="12" cy="12" r="9" fill="none" stroke="#1d2a4d" stroke-width="2"/><path d="M3 12h18M12 3c3 3 3 15 0 18M12 3c-3 3-3 15 0 18" fill="none" stroke="#1d2a4d" stroke-width="1.6"/></svg>
      www.groutandgrade.com.au
    </span>
  </div>

  <main class="letter-body">
    <p class="salutation">Dear Mr. Carter,</p>
    <p class="para">Lorem ipsum dolor sit amet, consectetur adipiscing elit. Donec orci purus, luctus vitae dignissim eu, iaculis sed purus. Vivamus facilisis, ipsum nec aliquet viverra, leo mauris condimentum ligula, sit amet sagittis enim ligula quis arcu. Nam egestas tortor id nisl porttitor mattis, in tortor ante, ultricies in suscipit a, tempor non massa. Vivamus et auctor mi. Fusce vel massa nulla. Phasellus nec ante mauris, at volutpat nisi.</p>
    <p class="para">Donec malesuada est vitae nulla accumsan pretium id massa. Quisque accumsan iaculis magna sit amet fringilla. Maecenas consequat, magna eget tincidunt semper, odio nibh rutrum nisi, id feugiat ante nisl eu risus. Vestibulum nunc orci, rhoncus at placerat in, ultricies in est. Cras mattis odio eros, vel fringilla nisi suscipit eget. Quisque scelerisque sagittis nulla at porttitor.</p>
    <p class="para">Sed id augue vitae eros euismod commodo aliquet a quam. Pellentesque arcu velit, cursus et malesuada sit, consequat et diam. Nullam erat eros, rhoncus id ullamcorper vitae, rhoncus et arcu. In ultricies ultricies nulla, ut rutrum nisi iaculis at. Donec consequat, ornare ornare faucibus. Fusce aliquet faucibus ultricies. Morbi semper, est id tincidunt gravida, nunc arcu adipiscing lacus, ac bibendum nulla leo eu purus. Quisque nec diam sed risus consectetur a ornare quis odio.</p>
    <p class="para">It is a long established fact that a reader will be distracted by the readable content of a page when looking at its layout. The point of using Lorem Ipsum is that it has a more-or-less normal distribution of letters, as opposed to using 'Content here, content here', making it look like readable English. Many desktop publishing packages.</p>
    <div class="sign-off">
      <p>Sincerely,</p>
      <div class="signature-mark" role="img" aria-label="Handwritten signature"></div>
      <p class="signer">Alan Carter<br>CEO/Founder</p>
    </div>
  </main>
</body>
</html>
```